Corporate Travel Technology Company needs new Business Card design

We need a new business card design to reflect our re-branded company. Our company is called tolvEn (pronounced tolvenn) and we provide Business Intelligence and mobile travel management solutions for the corporate travel industry. Our multinational customers use our solutions to manage large travel budgets and frequent travellers, as well as to save money and reduce risk. We'd like to see designs that use the blue and green palette as well as our corporate logo (attached below). The design should communicate innovation, insight, forward thinking, contemporary, trusted.

Target Market(s)

Large multinational corporates and Travel Agencies.

Industry/Entity Type

Business

Contact Information for Business Card

Rosalind Mercer
Chief Executive
tolvEn
Phone number - +61 (0)2 8134 2907
Email address - rosalind.mercer@tolven-example.com
Mobile number - +61 (0)438 516 702
www.tolven-example.com

Font styles to use
Other font styles liked:
• Please use font as close to corporate logo as possible

Colors
0255a3
0393ce
00a990
33b8a4
33a6d7
3176b5

Requirements
Must have
• Please include the words;
• Mobile Travel Management
• Accelerating Travel Business Insights
• Use corporate logo - although icon can be stylised if needed

```html
<!DOCTYPE html>
<html lang="en">
<head>
<meta charset="utf-8">
<title>tolvEn business card</title>
<link rel="stylesheet" href="https://fonts.googleapis.com/css2?family=Open+Sans:wght@400;600;700&display=swap">
<style>
  :root {
    --backdrop: #e9e7e3;
    --card: #ffffff;
    --slate: #475a58;
    --slate-dark: #3f504e;
    --sky: #25a6df;
    --text: #3a4644;
  }
  * { box-sizing: border-box; margin: 0; padding: 0; }
  html, body { width: 1200px; height: 750px; overflow: hidden; }
  body {
    background: var(--backdrop);
    font-family: "Open Sans", Arial, sans-serif;
    color: var(--text);
    position: relative;
  }
  .card {
    position: absolute;
    top: 200px;
    width: 558px;
    height: 320px;
    background: var(--card);
    border-radius: 18px;
    overflow: hidden;
    box-shadow: 0 4px 10px rgba(0,0,0,0.25);
  }
  .card--front { left: 30px; }
  .card--back { left: 613px; width: 559px; }

  .sphere {
    position: absolute;
    width: 320px;
    height: 320px;
    border-radius: 50%;
    background: var(--slate);
    top: 0;
  }
  .card--front .sphere { left: 410px; }
  .card--back .sphere { left: -173px; }

  .brand {
    position: absolute;
    font-weight: 600;
    color: var(--slate);
    line-height: 1;
    letter-spacing: -0.5px;
  }
  .brand__dot {
    position: absolute;
    border-radius: 50%;
    background: var(--sky);
  }
  .card--front .brand { left: 30px; top: 84px; font-size: 62px; }
  .card--front .brand__dot { left: 122px; top: 34px; width: 40px; height: 40px; }
  .card--back .brand { right: 34px; top: 132px; font-size: 84px; }
  .card--back .brand__dot { left: 348px; top: 62px; width: 58px; height: 58px; }

  .name-bar {
    position: absolute;
    left: 2px; top: 170px;
    width: 20px; height: 37px;
    background: var(--slate);
    border-right: 5px solid var(--sky);
  }
  .person__name {
    position: absolute;
    left: 32px; top: 166px;
    font-size: 21px;
    font-weight: 700;
    color: var(--slate-dark);
    letter-spacing: 0.3px;
  }
  .person__title {
    position: absolute;
    left: 32px; top: 193px;
    font-size: 14.5px;
    color: var(--sky);
  }
  .person__rule {
    position: absolute;
    left: 146px; top: 203px;
    width: 290px; height: 1px;
    background: var(--sky);
  }

  .contacts {
    position: absolute;
    left: 30px; top: 228px;
    list-style: none;
    font-size: 14.5px;
    line-height: 17.6px;
    color: var(--text);
  }
  .contacts li { display: flex; align-items: center; }
  .contacts svg { width: 12px; height: 12px; margin-right: 10px; flex: none; }

  .taglines {
    position: absolute;
    right: 34px; top: 233px;
    list-style: none;
    font-size: 15px;
    line-height: 20px;
    color: var(--text);
    text-align: right;
  }
  .taglines li { display: flex; justify-content: flex-end; align-items: center; }
  .taglines svg { width: 12px; height: 12px; margin-left: 5px; }
</style>
</head>
<body>

<section class="card card--front">
  <div class="sphere"></div>
  <span class="brand__dot"></span>
  <div class="brand">tolvEn</div>

  <div class="name-bar"></div>
  <h1 class="person__name">ROSALIND MERCER</h1>
  <p class="person__title">Chief Executive</p>
  <div class="person__rule"></div>

  <ul class="contacts">
    <li>
      <svg viewBox="0 0 12 12"><rect x="3" y="0.5" width="6" height="11" rx="1.2" fill="none" stroke="#25a6df" stroke-width="1.3"/><circle cx="6" cy="9.5" r="0.7" fill="#25a6df"/></svg>
      +61 (0)438 516 702
    </li>
    <li>
      <svg viewBox="0 0 12 12"><path d="M2.5 1 L4.5 1 L5.3 3.6 L4 4.6 C4.7 6.2 5.8 7.3 7.4 8 L8.4 6.7 L11 7.5 L11 9.5 C11 10.3 10.3 11 9.5 11 C5 10.6 1.4 7 1 2.5 C1 1.7 1.7 1 2.5 1 Z" fill="#25a6df"/></svg>
      +61 (0)2 8134 2907
    </li>
    <li>
      <svg viewBox="0 0 12 12"><circle cx="6" cy="6" r="5" fill="none" stroke="#25a6df" stroke-width="1"/><ellipse cx="6" cy="6" rx="2.2" ry="5" fill="none" stroke="#25a6df" stroke-width="1"/><line x1="1" y1="6" x2="11" y2="6" stroke="#25a6df" stroke-width="1"/></svg>
      www.tolven-example.com
    </li>
    <li>
      <svg viewBox="0 0 12 12"><rect x="0.8" y="2.5" width="10.4" height="7.5" fill="none" stroke="#25a6df" stroke-width="1.1"/><path d="M0.8 2.5 L6 6.8 L11.2 2.5" fill="none" stroke="#25a6df" stroke-width="1.1"/></svg>
      rosalind.mercer@tolven-example.com
    </li>
  </ul>
</section>

<section class="card card--back">
  <div class="sphere"></div>
  <span class="brand__dot"></span>
  <div class="brand">tolvEn</div>

  <ul class="taglines">
    <li>Mobile Travel Management
      <svg viewBox="0 0 12 12"><path d="M1 2 L11 2 L6 11 Z" fill="none" stroke="#25a6df" stroke-width="1.4" stroke-linejoin="round"/></svg>
    </li>
    <li>Accelerating Travel Business Insights
      <svg viewBox="0 0 12 12"><path d="M1 2 L11 2 L6 11 Z" fill="none" stroke="#25a6df" stroke-width="1.4" stroke-linejoin="round"/></svg>
    </li>
  </ul>
</section>

</body>
</html>
```